TK Homes - Stone Dorf Design

Looking for a double sides design, 1 side for my realestate and the other for home building. ( TK Homes on 1 side, Stone Dorf card on the other Side
Side 1 - Marek Tove ~ Vox Realty logo and Company ( the Property quarter )
Marek Tove
Marek@Marektove.example
IG - Marek_Bzq_Realtor
FB - marekt
Cell - 5558130467
3847 61 St Nw

Side 2
Marek Tove
5558130467
IG - Stonedorf_Bzq
Stonedorfdev@mailbox.example

Target Market(s)

Home buyers/ sellers

Industry/Entity Type

Home builders - Realestate

Contact Information for Business Card

Above

Requirements
Must have
• Black OR White background - my information -

```html
<!DOCTYPE html>
<html lang="en">
<head>
<meta charset="utf-8">
<title>Marek Tove – Business Cards</title>
<link rel="stylesheet" href="https://fonts.googleapis.com/css2?family=Cinzel:wght@400;600&family=Tinos&display=swap">
<style>
  :root {
    --page: #111112;
    --card: #1c1c1e;
    --ink: #f2f2f2;
    --blue: #1f7ac4;
    --muted: #cfcfcf;
  }
  * { margin: 0; padding: 0; box-sizing: border-box; }
  html, body { width: 1200px; height: 1059px; overflow: hidden; background: var(--page); }
  .canvas { position: relative; width: 1200px; height: 1059px; }

  .card {
    position: absolute;
    background: var(--card);
    border-radius: 20px;
  }
  .card--realty { left: 257px; top: 89px; width: 687px; height: 390px; }
  .card--builder { left: 254px; top: 547px; width: 693px; height: 393px; }

  .divider {
    position: absolute;
    width: 1.5px;
    background: var(--blue);
  }
  .card--realty .divider { left: 343px; top: 102px; height: 188px; }
  .card--builder .divider { left: 346px; top: 125px; height: 145px; }

  .brand {
    position: absolute;
    display: flex;
    flex-direction: column;
    align-items: center;
    transform: translateX(-50%);
  }
  .brand-mark {
    width: 54px; height: 54px;
    border: 2px solid var(--blue);
    margin-bottom: 16px;
  }
  .brand-name {
    font-family: "Cinzel", serif;
    font-weight: 600;
    white-space: nowrap;
  }
  .card--realty .brand { left: 196px; top: 96px; }
  .card--realty .brand-name { color: var(--blue); font-size: 36px; letter-spacing: 1px; }

  .partners {
    display: flex;
    gap: 22px;
    margin-top: 18px;
  }
  .partner {
    font-family: "Cinzel", serif;
    font-weight: 600;
    font-size: 12px;
    color: var(--ink);
    white-space: nowrap;
  }

  .card--builder .brand { left: 193px; top: 140px; }
  .card--builder .brand-mark { border-color: var(--ink); width: 46px; height: 46px; margin-bottom: 18px; }
  .card--builder .brand-name { color: var(--ink); font-size: 34px; letter-spacing: 2px; }

  .holder {
    position: absolute;
    font-family: "Cinzel", serif;
    font-weight: 400;
    font-size: 30px;
    color: var(--ink);
    letter-spacing: 0.5px;
    white-space: nowrap;
  }
  .card--realty .holder { left: 374px; top: 94px; }
  .card--builder .holder { left: 376px; top: 112px; }

  .contacts { position: absolute; list-style: none; }
  .card--realty .contacts { left: 374px; top: 155px; }
  .card--builder .contacts { left: 376px; top: 172px; }
  .contact {
    display: flex;
    align-items: center;
    gap: 8px;
    font-family: "Tinos", serif;
    font-size: 18px;
    color: var(--ink);
    white-space: nowrap;
  }
  .card--realty .contact { height: 23.3px; }
  .card--builder .contact { height: 26.5px; }
  .icon { width: 13px; height: 13px; flex: none; fill: var(--blue); }
</style>
</head>
<body>
<main class="canvas">

  <section class="card card--realty" aria-label="Real estate side">
    <div class="brand">
      <span class="brand-mark"></span>
      <span class="brand-name">MAREK TOVE</span>
      <div class="partners">
        <span class="partner">the Property quarter</span>
        <span class="partner">Vox Realty</span>
      </div>
    </div>
    <span class="divider"></span>
    <h1 class="holder">MAREK TOVE</h1>
    <ul class="contacts">
      <li class="contact"><svg class="icon" viewBox="0 0 16 16"><path d="M4 1l3 3-2 2c1 2 3 4 5 5l2-2 3 3-2 3C7 15 1 9 1 3z"/></svg>5558130467</li>
      <li class="contact"><svg class="icon" viewBox="0 0 16 16"><path d="M1 6l7-5 7 5v9H1z M2 7l6 4 6-4" /></svg>Marek@Marektove.example</li>
      <li class="contact"><svg class="icon" viewBox="0 0 16 16"><circle cx="8" cy="8" r="7"/></svg>www.Marektove.example</li>
      <li class="contact"><svg class="icon" viewBox="0 0 16 16"><path d="M8 0a5.5 5.5 0 0 1 5.5 5.5C13.5 10 8 16 8 16S2.5 10 2.5 5.5A5.5 5.5 0 0 1 8 0zm0 3.3a2.2 2.2 0 1 0 0 4.4 2.2 2.2 0 0 0 0-4.4z"/></svg>3847 61 St Nw</li>
      <li class="contact"><svg class="icon" viewBox="0 0 16 16"><rect x="1" y="1" width="14" height="14" rx="3"/></svg>Marek_Bzq_Realtor</li>
      <li class="contact"><svg class="icon" viewBox="0 0 16 16"><circle cx="8" cy="8" r="7"/></svg>marekt</li>
    </ul>
  </section>

  <section class="card card--builder" aria-label="Home building side">
    <div class="brand">
      <span class="brand-mark"></span>
      <span class="brand-name">STONE DORF</span>
    </div>
    <span class="divider"></span>
    <h2 class="holder">MAREK TOVE</h2>
    <ul class="contacts">
      <li class="contact"><svg class="icon" viewBox="0 0 16 16"><path d="M4 1l3 3-2 2c1 2 3 4 5 5l2-2 3 3-2 3C7 15 1 9 1 3z"/></svg>5558130467</li>
      <li class="contact"><svg class="icon" viewBox="0 0 16 16"><path d="M1 6l7-5 7 5v9H1z"/></svg>Stonedorfdev@mailbox.example</li>
      <li class="contact"><svg class="icon" viewBox="0 0 16 16"><circle cx="8" cy="8" r="7"/></svg>www.stonedorfdev.example</li>
      <li class="contact"><svg class="icon" viewBox="0 0 16 16"><rect x="1" y="1" width="14" height="14" rx="3"/></svg>Stonedorf_Bzq</li>
    </ul>
  </section>

</main>
</body>
</html>
```